Push notification screens at app start up

We have an existing news publication app platform and are adding categories to push notifications.

We need two screens designed (each for Zorbel, Quillet and Android for a total of 6d) that show when the app is first launched.

The workflow of our app:
0. app launch screen while webservices run (no work needed)
1. information screen to the user promoting the benefits of push notification with "Next" button. (see concept attached)
2. Push categories selection screen. This will have list of category types, with on/off switch.

"Select the categories that you wish to receive occasional notices:
Breaking News (on/off switch)
Local News (on/off switch)
Sports (on/off switch)
Local Events (on/off switch)
Weather Alerts (on/off switch)
Local Deals (on/off switch)"

"Enable these categories on the next screen."
"Next" button

Background:
When I was looking around at app designs, I came across this one (http://www.plinthworks.example/design/7719034) and I really liked it. We obviously have different features on our screen, but I’d like to have this same feel. The colors used in this design are perfect.

UPDATE: I do not mean to limit your design to match the layout as the one mentioned above. Please use your creativity for the layout.

Our standard font in Helvetica Neue.

Notes:
- our app is developed for all phone devices from Zorbel 4 to Zorbel 6, so designs should be thoughtful of vertical scrolling if needed.
- our app is developed for Quillets, so we'll need designs completed as well. (We can finalize Zorbel design first, then translate the design to Quillet.)
- our app is developed for Android phones (not tablets), so we'll need designs completed as well. (We can finalize iOS design first, then translater to Android UI design guidelines).

We hope to establish a good on-going relationship with the designer for as-needed work in the future.

News

• Helvetica Neue

• Clean designs. No clutter.
• We would likely go with the standard on/off switches for both iOS and Android, but are open to small custom variations.

```html
<!DOCTYPE html>
<html lang="en">
<head>
<meta charset="utf-8">
<title>Notifications</title>
<link rel="stylesheet" href="https://fonts.googleapis.com/css2?family=Inter:wght@400;700&display=swap">
<style>
  :root {
    --brand-red: #e8202a;
    --card-grey: #bcbcbc;
    --ink: #1f1f1f;
    --status-ink: #c4c4c4;
    --screen-bg: #ffffff;
    --white: #ffffff;
  }
  html, body {
    margin: 0;
    padding: 0;
    overflow: hidden;
    background: var(--screen-bg);
  }
  .screen {
    position: relative;
    width: 675px;
    height: 1200px;
    overflow: hidden;
    background: var(--screen-bg);
    font-family: "Inter", "Helvetica Neue", Helvetica, Arial, sans-serif;
    color: var(--ink);
  }
  .status-bar {
    position: absolute;
    top: 10px;
    left: 22px;
    right: 22px;
    height: 30px;
    display: flex;
    justify-content: space-between;
    align-items: center;
    font-size: 20px;
    color: var(--status-ink);
  }
  .status-bar .time { position: absolute; left: 0; right: 0; text-align: center; }
  .info-card {
    position: absolute;
    left: 27px;
    top: 207px;
    width: 621px;
    height: 659px;
    background: var(--card-grey);
    border-radius: 22px;
  }
  .badge {
    position: absolute;
    left: 240px;
    top: 72px;
    width: 195px;
    height: 195px;
    border-radius: 50%;
    background: var(--brand-red);
    display: flex;
    align-items: center;
    justify-content: center;
  }
  .info-title {
    position: absolute;
    top: 337px;
    left: 0;
    width: 675px;
    margin: 0;
    text-align: center;
    font-size: 40px;
    font-weight: 700;
  }
  .info-body {
    position: absolute;
    top: 410px;
    left: 0;
    width: 675px;
    text-align: center;
    font-size: 23.5px;
    line-height: 34.5px;
  }
  .info-body p { margin: 0 0 34.5px; }
  .next-button {
    position: absolute;
    left: 27px;
    top: 916px;
    width: 621px;
    height: 96px;
    border: 0;
    border-radius: 12px;
    background: var(--brand-red);
    color: var(--white);
    font-family: inherit;
    font-size: 38px;
    font-weight: 700;
    letter-spacing: 0.5px;
  }
</style>
</head>
<body>
<main class="screen">
  <div class="status-bar">
    <span class="carrier">●●●○○ NORTH</span>
    <span class="time">4:21 PM</span>
    <span class="battery">100%</span>
  </div>

  <section class="info-card" aria-label="Notifications information"></section>

  <div class="badge">
    <svg class="megaphone-icon" width="120" height="100" viewBox="0 0 120 100" aria-hidden="true">
      <g fill="none" stroke="#ffffff" stroke-width="6" stroke-linejoin="round" stroke-linecap="round">
        <rect x="6" y="36" width="18" height="28" rx="3"/>
        <path d="M24 38 L70 14 L70 86 L24 62 Z"/>
        <path d="M30 62 L38 88 L50 88 L44 66"/>
        <path d="M82 38 Q90 50 82 62"/>
        <path d="M92 28 Q106 50 92 72"/>
        <path d="M102 18 Q122 50 102 82"/>
      </g>
      <g stroke="#ffffff" stroke-width="4">
        <line x1="36" y1="40" x2="36" y2="60"/>
        <line x1="46" y1="34" x2="46" y2="66"/>
      </g>
    </svg>
  </div>

  <h1 class="info-title">Notifications</h1>

  <div class="info-body">
    <p>By enabling push notifications, you can<br>keep up to date with occasional<br>notifications related to items you care<br>about. Select the categories on the<br>next screen and then authorize the<br>push notifications.</p>
    <p>If you ever change your mind, you can<br>adjust these options in the Settings<br>menu of this app.</p>
  </div>

  <button class="next-button" type="button">NEXT</button>
</main>
</body>
</html>
```